Book cover

I am working with my publisher to publish my book They came up with a book cover but I don't like it. I want to see different designs. The book Title is Brightwater the subtitle Ways to Guide Teams Through Storms with Poise, Purpose & Pace by Marlene T. Ostrowski
I want to use my Brand Colors including the blue. I am uploading the covers of my other book. This is a professional leadership book. The publisher will make the cover when providing them a new design. the Brightwater one is one I played with on Canva. I would like more color and to incorporate the blue. I want a spot at the top where I can write a quote. Brightwater is one word in the text so should be the same on the cover. I want the cover to show energy movement and am open to an image too. I am attaching logos for the feel of the brand and brand rgb codes.

```html
<!DOCTYPE html>
<html lang="en">
<head>
<meta charset="utf-8">
<title>Brightwater — Book Cover</title>
<link href="https://fonts.googleapis.com/css2?family=Yellowtail&family=Quicksand:wght@500;600&display=swap" rel="stylesheet">
<style>
  :root {
    --stage: #000000;
    --paper: #ffffff;
    --brand-blue: #0033a0;
    --brand-sky: #3fb6e8;
    --wave-light: #cfeaf8;
    --wave-mid: #6cc3ea;
    --wave-deep: #1f4f8f;
    --wave-teal: #2aa7c9;
    --author-text: #ffffff;
  }
  * { margin: 0; padding: 0; box-sizing: border-box; }
  html, body {
    width: 1200px;
    height: 1200px;
    overflow: hidden;
    background: var(--stage);
  }
  .book-cover {
    position: absolute;
    left: 232px;
    top: 46px;
    width: 741px;
    height: 1111px;
    background: var(--paper);
    overflow: hidden;
  }
  .cover-quote {
    position: absolute;
    top: 38px;
    left: 90px;
    width: 561px;
    padding: 10px 0;
    border-top: 2px solid var(--brand-sky);
    border-bottom: 2px solid var(--brand-sky);
    text-align: center;
    font-family: "Quicksand", sans-serif;
    font-weight: 500;
    font-style: normal;
    font-size: 17px;
    line-height: 24px;
    color: var(--brand-blue);
  }
  .cover-title {
    position: absolute;
    top: 138px;
    left: 20px;
    width: 701px;
    text-align: center;
    white-space: nowrap;
    font-family: "Yellowtail", "Brush Script MT", cursive;
    font-weight: 400;
    font-size: 128px;
    line-height: 1.1;
    color: var(--brand-blue);
  }
  .energy-wave {
    position: absolute;
    left: 0;
    top: 400px;
    width: 100%;
    height: 270px;
    background:
      radial-gradient(ellipse 40% 26% at 26% 66%, var(--wave-mid) 0%, rgba(108,195,234,0) 72%),
      radial-gradient(ellipse 34% 20% at 62% 40%, var(--wave-deep) 0%, rgba(31,79,143,0) 72%),
      radial-gradient(ellipse 26% 22% at 84% 58%, var(--wave-teal) 0%, rgba(42,167,201,0) 72%),
      radial-gradient(ellipse 75% 45% at 50% 52%, var(--wave-light) 0%, rgba(207,234,248,0) 78%);
  }
  .cover-subtitle {
    position: absolute;
    top: 790px;
    left: 0;
    width: 100%;
    text-align: center;
    font-family: "Quicksand", sans-serif;
    font-weight: 600;
    font-size: 27px;
    line-height: 38px;
    color: var(--brand-blue);
  }
  .author-band {
    position: absolute;
    left: 0;
    bottom: 0;
    width: 100%;
    height: 102px;
    background: var(--brand-blue);
    display: flex;
    align-items: center;
    justify-content: center;
  }
  .author-name {
    font-family: "Quicksand", sans-serif;
    font-weight: 600;
    font-size: 40px;
    color: var(--author-text);
    letter-spacing: 0.5px;
  }
</style>
</head>
<body>
  <main class="book-cover">
    <p class="cover-quote">“A steady hand turns rough water into a clear course.”</p>
    <h1 class="cover-title">Brightwater</h1>
    <div class="energy-wave" role="img" aria-label="Flowing abstract blue wave with sparkling light particles, suggesting energy and movement"></div>
    <p class="cover-subtitle">Ways to Guide Teams Through Storms<br>with Poise, Purpose &amp; Pace</p>
    <footer class="author-band">
      <span class="author-name">Marlene T. Ostrowski</span>
    </footer>
  </main>
</body>
</html>
```